Local fast-growing company in the service sector

We are looking for a modern business card design, which should also appear on our letterheads

Target Market(s)

Private and industrial sectors

Contact Information for Business Card

Vorname Name
Kellberger Str. 18
74389 Bergstetten
Tel.: 07146-839214-0
Name@agentur-kvtl.de

Colors
9d9d9d
919191
aaaaaa

Requirements
Must have
• The logo (file) in silver

```html
<!DOCTYPE html>
<html lang="de">
<head>
<meta charset="utf-8">
<title>KVTL Visitenkarte</title>
<link rel="stylesheet" href="https://fonts.googleapis.com/css2?family=Open+Sans:wght@400;600;700&display=swap">
<style>
  :root {
    --backdrop: #2b2624;
    --card: #0c0c0c;
    --card-edge: #1a1a1a;
    --silver: #9d9d9d;
    --silver-mid: #919191;
    --silver-light: #aaaaaa;
    --text-light: #d8d8d8;
  }
  * { box-sizing: border-box; margin: 0; padding: 0; }
  html, body {
    width: 1200px; height: 844px; overflow: hidden;
    background: var(--backdrop);
    font-family: "Open Sans", Arial, sans-serif;
  }
  .stage { position: relative; width: 1200px; height: 844px; }
  .card {
    position: absolute; top: 247px;
    width: 540px; height: 350px;
    background: var(--card);
    border: 1px solid var(--card-edge);
    box-shadow: 0 10px 30px rgba(0,0,0,.45);
  }
  .card--front { left: 40px; }
  .card--back { left: 620px; }

  .brand { display: flex; align-items: center; gap: 14px; color: var(--silver); }
  .brand__mark { width: 40px; height: 40px; background: var(--silver-mid); }
  .brand__name { font-weight: 700; font-size: 52px; letter-spacing: 1px; line-height: 1; }
  .card--front .brand { position: absolute; left: 46px; top: 62px; }
  .card--back .brand { position: absolute; left: 50%; top: 50%; transform: translate(-50%, -50%); }

  .contact {
    position: absolute; right: 34px; top: 138px;
    list-style: none; text-align: right;
    color: var(--text-light); font-size: 14px; line-height: 20px;
  }
  .contact li { display: flex; justify-content: flex-end; align-items: center; gap: 6px; }
  .contact svg { width: 11px; height: 11px; fill: var(--silver); }

  .person { position: absolute; left: 46px; bottom: 50px; }
  .person__name { color: var(--silver); font-weight: 600; font-size: 19px; margin-bottom: 16px; }
  .person__address { font-style: normal; color: var(--text-light); font-size: 15px; line-height: 21px; }
</style>
</head>
<body>
<main class="stage">
  <section class="card card--front" aria-label="Vorderseite">
    <div class="brand">
      <span class="brand__mark"></span>
      <span class="brand__name">KVTL</span>
    </div>

    <ul class="contact">
      <li>07146-839214-0
        <svg viewBox="0 0 12 12" aria-hidden="true"><path d="M2.5 0.5l2 2.2-1 1.3c.7 1.6 2 2.9 3.6 3.6l1.3-1 2.2 2-1.2 2.2C4.8 10.6 1.4 7.2 0.4 1.7z"/></svg>
      </li>
      <li>Name@agentur-kvtl.de
        <svg viewBox="0 0 12 12" aria-hidden="true"><path d="M0 2h12v8H0z M1 3l5 3.5L11 3" fill="none" stroke="#9d9d9d" stroke-width="1.2"/></svg>
      </li>
      <li>www.agentur-kvtl.de
        <svg viewBox="0 0 12 12" aria-hidden="true"><circle cx="6" cy="6" r="5.5"/></svg>
      </li>
    </ul>

    <div class="person">
      <p class="person__name">Vorname Name</p>
      <address class="person__address">Kellberger Str. 18<br>74389 Bergstetten</address>
    </div>
  </section>

  <section class="card card--back" aria-label="Rückseite">
    <div class="brand">
      <span class="brand__mark"></span>
      <span class="brand__name">KVTL</span>
    </div>
  </section>
</main>
</body>
</html>
```